Quobrin homepage

Re-design www.quobrin.com. Visitors are developers and CTOs. Something simple and straightforward. Need different and special landingpage.
I like this page: http://plinthwave.io/ (service is also similar).
Logo is at http://www.quobrin.com/quobrin.svg
Be bold with content you see on www.quobrin.com.
If you want ... make main message shorter, add links that doesn't exist, remove something etc.
Landing page should be cleaner than it is now.
Things what I want to have on page (missing on quobrin.com):
- testimonials
- contact form (can be simple as "send us e-mail...")
Quobrin supports TreBase, KestrumDB, Nubrix and HX Dorn. You are welcome to use logos for those databases.
CTO-s and developers/programmers
It Service

```html
<!DOCTYPE html>
<html lang="en">
<head>
<meta charset="utf-8">
<title>Quobrin — Boost Up Your Creation</title>
<link href="https://fonts.googleapis.com/css2?family=Roboto:wght@300;400;500&display=swap" rel="stylesheet">
<style>
  :root {
    --teal: #1ba3c6;
    --teal-deep: #12869f;
    --teal-hero-a: #0f7f98;
    --teal-hero-b: #2aaac4;
    --ink: #333a3f;
    --nav-ink: #3d3d3d;
    --muted: #b8b8b8;
    --line: #dcdcdc;
    --white: #ffffff;
  }
  * { box-sizing: border-box; margin: 0; padding: 0; }
  html, body { width: 1200px; height: 975px; overflow: hidden; background: var(--white); }
  body { font-family: "Roboto", Arial, sans-serif; color: var(--ink); position: relative; }

  .site-header {
    height: 86px; display: flex; align-items: center; justify-content: space-between;
    padding: 0 67px 0 70px; border-bottom: 2px solid #d8e6ea; position: relative; z-index: 2;
  }
  .brand { display: flex; align-items: center; gap: 10px; text-decoration: none; }
  .brand-mark { width: 22px; height: 22px; background: var(--teal); }
  .brand-name { font-size: 26px; font-weight: 400; color: #2f3336; letter-spacing: 0.5px; }
  .main-nav { display: flex; gap: 26px; list-style: none; }
  .main-nav a { font-size: 16px; font-weight: 400; color: var(--nav-ink); text-decoration: none; }
  .main-nav a.is-active { color: var(--teal); }

  .hero {
    position: absolute; top: 86px; left: 0; width: 1200px; height: 559px;
    text-align: center; color: var(--white); overflow: hidden;
  }
  .hero-backdrop {
    position: absolute; inset: 0;
    background:
      linear-gradient(150deg, transparent 55%, rgba(255,255,255,0.06) 55%),
      linear-gradient(180deg, var(--teal-hero-a) 0%, #1d93ad 45%, var(--teal-hero-b) 100%);
  }
  .hero-content { position: relative; }
  .hero-badge {
    width: 56px; height: 56px; border-radius: 50%; margin: 128px auto 0;
    background: rgba(255,255,255,0.35);
  }
  .hero-title { font-size: 36px; font-weight: 500; margin-top: 16px; line-height: 44px; }
  .hero-lead {
    font-size: 23px; font-weight: 300; line-height: 32px; margin: 42px auto 0; width: 740px;
  }
  .hero-lead strong { font-weight: 400; }
  .cta {
    display: inline-flex; align-items: center; gap: 14px; margin-top: 36px;
    height: 50px; padding: 0 34px 0 42px; border-radius: 25px;
    background: rgba(10,70,90,0.55); color: var(--white); text-decoration: none;
    font-size: 22px; font-weight: 500;
  }
  .cta-dots { display: flex; gap: 10px; margin-left: 8px; }
  .cta-dots span { width: 16px; height: 16px; border-radius: 50%; border: 2px solid rgba(255,255,255,0.75); }

  .db-strip {
    position: absolute; top: 645px; left: 0; width: 1200px; height: 101px;
    border-bottom: 1px solid var(--line);
    display: flex; justify-content: center; align-items: center; gap: 70px;
  }
  .db-name { font-size: 27px; font-weight: 400; color: var(--muted); }

  .features { position: absolute; top: 746px; left: 0; width: 1200px; text-align: center; }
  .features-title { font-size: 25px; font-weight: 500; color: var(--ink); margin-top: 48px; }
  .feature-icons { list-style: none; position: relative; height: 200px; }
  .feature-icon {
    position: absolute; top: 160px; width: 80px; height: 80px; border-radius: 50%;
    background: var(--teal); overflow: hidden;
    display: flex; align-items: center; justify-content: center;
  }
  .feature-icon::after {
    content: ""; position: absolute; left: 40px; top: 40px; width: 80px; height: 80px;
    background: var(--teal-deep); opacity: 0.45; transform: rotate(-45deg); transform-origin: 0 0;
  }
  .feature-icon svg { position: relative; z-index: 1; }
  .feature-icon .js-label { position: relative; z-index: 1; color: var(--white); font-size: 26px; font-weight: 500; }
</style>
</head>
<body>
  <header class="site-header">
    <a class="brand" href="#">
      <span class="brand-mark"></span>
      <span class="brand-name">quobrin</span>
    </a>
    <ul class="main-nav">
      <li><a class="is-active" href="#">Home</a></li>
      <li><a href="#">About</a></li>
      <li><a href="#">Installation</a></li>
      <li><a href="#">Documentation</a></li>
      <li><a href="#">Benefits</a></li>
      <li><a href="#">Compare</a></li>
      <li><a href="#">Download</a></li>
    </ul>
  </header>

  <section class="hero">
    <div class="hero-backdrop" role="img" aria-label="Blurred photo of a laptop on a desk, tinted teal"></div>
    <div class="hero-content">
      <div class="hero-badge"></div>
      <h1 class="hero-title">Boost Up Your Creation</h1>
      <p class="hero-lead"><strong>Quobrin</strong> speed up building mobile apps, JavaScript heavy interfaces and integrations by reducing amount of code and todo list.</p>
      <a class="cta" href="#">Get Quobrin
        <span class="cta-dots"><span></span><span></span><span></span></span>
      </a>
    </div>
  </section>

  <section class="db-strip" aria-label="Supported databases">
    <span class="db-name">TreBase</span>
    <span class="db-name">KestrumDB</span>
    <span class="db-name">Nubrix</span>
    <span class="db-name">HX Dorn</span>
  </section>

  <section class="features">
    <h2 class="features-title">What can you do with Quobrin</h2>
    <ul class="feature-icons">
      <li class="feature-icon" style="left:117px">
        <svg width="38" height="36" viewBox="0 0 38 36" fill="none" stroke="#fff" stroke-width="3">
          <rect x="2" y="2" width="34" height="23" rx="2"/><path d="M19 25v7M11 33h16"/>
        </svg>
      </li>
      <li class="feature-icon" style="left:294px">
        <svg width="22" height="38" viewBox="0 0 22 38" fill="none" stroke="#fff" stroke-width="3">
          <rect x="2" y="2" width="18" height="34" rx="3"/><circle cx="11" cy="30" r="1.5" fill="#fff"/>
        </svg>
      </li>
      <li class="feature-icon" style="left:470px">
        <svg width="36" height="34" viewBox="0 0 36 34" fill="none" stroke="#fff" stroke-width="3">
          <path d="M3 31 12 18 20 24 33 5"/><circle cx="12" cy="18" r="3" fill="#fff"/><circle cx="20" cy="24" r="3" fill="#fff"/><circle cx="33" cy="5" r="3" fill="#fff"/>
        </svg>
      </li>
      <li class="feature-icon" style="left:644px"><span class="js-label">JS</span></li>
      <li class="feature-icon" style="left:823px">
        <svg width="36" height="36" viewBox="0 0 36 36" fill="none" stroke="#fff" stroke-width="3" stroke-linejoin="round">
          <path d="M18 4 33 11 18 18 3 11Z"/><path d="M3 11v14l15 7 15-7V11M18 18v14"/>
        </svg>
      </li>
      <li class="feature-icon" style="left:999px">
        <svg width="38" height="32" viewBox="0 0 38 32" fill="none" stroke="#fff" stroke-width="3">
          <rect x="2" y="2" width="34" height="28"/><path d="M2 9h34"/><rect x="8" y="14" width="12" height="10"/><path d="M24 15h7M24 20h7"/>
        </svg>
      </li>
    </ul>
  </section>
</body>
</html>
```